Bramble Hockey Academy

We are are Ice Hockey Development Company that provided on-ice Hockey development services. We need a Landing Page with tabs to direct to individual program pages.
Landing Page
About Page
Winter Program Page
Spring Program Page
Summer Program Page
Team Page
Tournament Page

Coded - Design and coding required

5+ page

```html
<!DOCTYPE html>
<html lang="en">
<head>
<meta charset="utf-8">
<title>Bramble Hockey Development</title>
<link href="https://fonts.googleapis.com/css2?family=Krona+One&family=Lato:wght@400;700&display=swap" rel="stylesheet">
<style>
:root{
  --green:#0b6b12;
  --green-bright:#1e8a22;
  --ink:#111;
  --muted:#444;
  --white:#fff;
  --black:#000;
}
*{margin:0;padding:0;box-sizing:border-box}
html,body{width:1200px;height:3460px;overflow:hidden;background:var(--white)}
body{position:relative;font-family:'Lato',sans-serif;color:var(--ink)}
.abs{position:absolute}
.display{font-family:'Krona One',sans-serif;text-transform:uppercase}

/* header */
.brand{left:112px;top:22px;font-family:'Krona One',sans-serif;font-size:24px;line-height:30px;color:var(--ink);text-transform:uppercase}
.info{top:18px;display:flex;gap:12px;align-items:center}
.info svg{width:34px;height:34px}
.info small{display:block;font-family:'Krona One',sans-serif;font-size:11px;color:var(--green)}
.info b{font-family:'Krona One',sans-serif;font-size:11px;color:var(--ink);font-weight:400}
.divider{left:694px;top:16px;width:1px;height:40px;background:#ccc}
.btn-contact{left:961px;top:12px;width:128px;height:43px;background:var(--green);clip-path:polygon(10% 0,100% 0,100% 100%,0 100%);color:#fff;font-family:'Krona One',sans-serif;font-size:12px;display:flex;align-items:center;justify-content:center;padding-left:10px}
.navbar{left:390px;top:68px;width:810px;height:62px;background:var(--green);clip-path:polygon(54px 0,100% 0,100% 100%,0 100%);border-top:3px solid #ddd;z-index:5}
.navbar a{position:absolute;top:21px;color:#fff;text-decoration:none;font-family:'Krona One',sans-serif;font-size:13px}
.navbar a.active{text-decoration:underline}

/* hero */
.hero{left:0;top:102px;width:1200px;height:628px;background:radial-gradient(ellipse at 72% 45%,#5b7590 0%,#2b4562 35%,#14253a 70%,#0a1522 100%)}
.hero-text{left:110px;top:214px;color:#fff}
.hero-text .kicker{font-family:'Krona One',sans-serif;font-size:21px;text-transform:uppercase}
.hero-text h1{font-family:'Krona One',sans-serif;font-size:36px;line-height:52px;font-weight:400;margin-top:4px;text-transform:uppercase}
.hero-text p{font-size:15px;line-height:26px;width:400px;margin-top:14px}
.btn-light{left:112px;top:453px;width:153px;height:46px;background:#fff;clip-path:polygon(14px 0,100% 0,100% 100%,0 100%);color:var(--green);font-family:'Krona One',sans-serif;font-size:13px;display:flex;align-items:center;justify-content:center}
.dot{width:11px;height:11px;border-radius:50%;background:#888;top:623px}
.dot.on{background:#111}

/* headings */
.eyebrow{width:1200px;left:0;text-align:center;font-family:'Krona One',sans-serif;font-size:16px;color:var(--green);text-transform:uppercase}
.title{width:1200px;left:0;text-align:center;font-family:'Krona One',sans-serif;font-size:30px;color:var(--ink);text-transform:uppercase}
.rule{height:3px;background:var(--ink)}
.on-green .eyebrow,.on-green .title{color:#fff}

/* about */
.about-photo{left:110px;top:867px;width:452px;height:524px;background:#fff;box-shadow:0 4px 14px rgba(0,0,0,.25);padding:8px}
.about-photo div{width:100%;height:100%;background:linear-gradient(180deg,#1f4e8a 0%,#6d8fb3 45%,#dfe7ee 75%,#c8d3dc 100%)}
.about-copy{left:636px;top:862px;width:453px;font-size:14.5px;line-height:27.5px;color:var(--muted);text-align:justify}
.about-copy p+p{margin-top:27px}
.btn-green{left:636px;top:1339px;width:153px;height:45px;background:var(--green);clip-path:polygon(14px 0,100% 0,100% 100%,0 100%);color:#fff;font-family:'Krona One',sans-serif;font-size:13px;display:flex;align-items:center;justify-content:center}

/* programs */
.programs-bg{left:0;top:1461px;width:1200px;height:340px;background:linear-gradient(180deg,#0f5a14 0%,var(--green) 60%,#12801a 100%)}
.card{background:#fff;box-shadow:0 2px 10px rgba(0,0,0,.2);padding:8px;text-align:center}
.card.featured{border:1.5px solid var(--green)}
.card .img{height:191px;background:linear-gradient(180deg,#1a2d52 0%,#43608c 50%,#cfd9e3 80%,#eef2f5 100%)}
.card h3{font-family:'Krona One',sans-serif;font-weight:400;font-size:14px;margin-top:24px;text-transform:uppercase}
.card .league{font-size:12px;font-weight:700;color:var(--green);margin-top:14px}
.card .score{display:flex;justify-content:center;align-items:center;gap:30px;font-weight:700;font-size:22px;margin-top:8px}
.card .score i{font-style:normal;font-size:9px;font-weight:400}
.card p{font-size:12.5px;line-height:24px;color:var(--muted);margin:10px 14px 0}

/* team */
.member{top:2206px;width:183px;height:229px;border:3px solid var(--green);border-radius:8px;text-align:center}
.member .gap{position:absolute;left:22px;right:22px;top:-4px;height:6px;background:#fff}
.member .avatar{position:absolute;left:31px;top:-24px;width:116px;height:116px;border-radius:50%;background:linear-gradient(160deg,#d9dee3,#6f8aa3 60%,#2c3e55)}
.member h4{position:absolute;left:0;top:104px;width:100%;font-weight:400;font-size:17px;color:var(--green)}
.member .role{position:absolute;left:0;top:134px;width:100%;font-size:13px;color:var(--muted)}
.member .in{position:absolute;left:71px;top:170px;width:35px;height:35px;border-radius:50%;background:var(--green);color:#fff;font-weight:700;font-size:14px;display:flex;align-items:center;justify-content:center}

/* tournament */
.tour-bg{left:0;top:2503px;width:1200px;height:360px;background:linear-gradient(120deg,#177a1c,var(--green-bright) 45%,#15761a)}
.badge-ring{width:162px;height:162px;border-radius:50%;background:#fff;display:flex;align-items:center;justify-content:center;top:2641px}
.badge-ring span{width:96px;height:96px;border-radius:50%;background:#dfe5ea}
.arrow-btn{width:26px;height:26px;border-radius:50%;background:#fff;top:2709px;display:flex;align-items:center;justify-content:center}
.count{top:2708px;width:59px;height:59px;border:2px solid #fff;border-radius:3px;color:#fff;text-align:center}
.count b{display:block;font-size:20px;margin-top:5px}
.count small{font-size:13px}

/* footer */
.footer-bg{left:0;top:2860px;width:1200px;height:600px;background:var(--black)}
.footer-brand{left:0;width:1200px;top:2990px;text-align:center;font-family:'Krona One',sans-serif;font-size:28px;line-height:36px;color:#fff;text-transform:uppercase}
.fline{left:110px;width:979px;height:1px;background:#555}
.fcol{color:#fff}
.fcol h5{font-family:'Krona One',sans-serif;font-weight:400;font-size:14px;margin-bottom:10px;text-transform:uppercase}
.fcol p{font-size:14px;line-height:26px}
.fcol ul{list-style:none}
.fcol li{font-size:15px;height:34.4px;display:flex;gap:10px;align-items:flex-start}
.fcol li svg{margin-top:3px}
.social{top:3263px;width:28px;height:28px;border-radius:50%;background:#fff}
.ci{display:flex;gap:12px;align-items:flex-start;font-size:15px;line-height:26px}
.ci .ico{width:32px;height:32px;border-radius:50%;background:#fff;display:flex;align-items:center;justify-content:center;flex:none}
.copy{left:0;width:1200px;top:3417px;text-align:center;color:#fff;font-size:14px;font-weight:700}
</style>
</head>
<body>

<!-- header -->
<div class="abs brand">Bramble<br>Hockey</div>

<div class="abs info" style="left:462px">
  <svg viewBox="0 0 34 34" fill="none" stroke="#0b6b12" stroke-width="1.6"><rect x="3" y="12" width="28" height="19" rx="1"/><path d="M3 12l14 11 14-11"/></svg>
  <div><small>Send Us Email</small><b>info@bramblehockey.com</b></div>
</div>
<div class="abs divider"></div>
<div class="abs info" style="left:727px">
  <svg viewBox="0 0 34 34" fill="none" stroke="#0b6b12" stroke-width="1.6"><path d="M17 3a8 8 0 0 1 8 8c0 6-8 14-8 14S9 17 9 11a8 8 0 0 1 8-8z"/><circle cx="17" cy="11" r="3"/><path d="M9 22l-6 9h28l-6-9"/></svg>
  <div><small>Location</small><b>Bramble Hockey, US</b></div>
</div>
<div class="abs btn-contact">Contact Us</div>

<!-- hero -->
<div class="abs hero" role="img" aria-label="Hockey player skating on ice with a puck flying toward the viewer"></div>

<nav class="abs navbar">
  <a class="active" href="#" style="left:75px">Home</a>
  <a href="#" style="left:192px">About</a>
  <a href="#" style="left:316px">Programs</a>
  <a href="#" style="left:470px">Team</a>
  <a href="#" style="left:584px">Tournament</a>
</nav>

<div class="abs hero-text">
  <div class="kicker">Welcome To</div>
  <h1>Bramble Hockey<br>Development</h1>
  <p>Itaque earum rerum hic tenetur a sapiente delectus, ut aut reiciendis voluptatibus maiores alias consequatur aut perferendis doloribus asperiores repellat.</p>
</div>
<div class="abs btn-light">Get Started</div>
<div class="abs dot" style="left:570px"></div>
<div class="abs dot on" style="left:595px"></div>
<div class="abs dot" style="left:619px"></div>

<svg class="abs" style="left:0;top:540px" width="1200" height="195" viewBox="0 540 1200 195">
  <polygon points="0,712 298,640 601,726 898,585 1200,700 1200,735 0,735" fill="#fff"/>
  <polygon points="0,685 298,612 601,700 898,558 1200,672 1200,700 898,585 601,726 298,640 0,712" fill="#0b6b12"/>
</svg>

<!-- about -->
<div class="abs eyebrow" style="top:772px">What We Do</div>
<div class="abs rule" style="left:215px;top:815px;width:86px"></div>
<div class="abs title" style="top:798px">About Bramble Hockey</div>
<div class="abs rule" style="left:899px;top:815px;width:89px"></div>

<div class="abs about-photo"><div role="img" aria-label="Two hockey players battling for the puck in an arena"></div></div>
<div class="abs about-copy">
  <p>At vero eos et accusamus et iusto odio dignissimos ducimus qui blanditiis praesentium voluptatum deleniti atque corrupti quos dolores et quas molestias excepturi sint occaecati cupiditate non provident, similique sunt in culpa qui officia deserunt mollitia animi, id est laborum et dolorum fuga. Et harum quidem rerum facilis est et expedita distinctio. Nam libero tempore, cum soluta nobis est eligendi optio cumque nihil impedit quo minus id quod maxime placeat facere possimus, omnis voluptas assumenda est, omnis dolor repellendus.</p>
  <p>Temporibus autem quibusdam et aut officiis debitis aut rerum necessitatibus saepe eveniet ut et voluptates repudiandae sint et molestiae non recusandae. Itaque earum rerum hic tenetur a sapiente delectus, ut aut reiciendis voluptatibus maiores alias consequatur aut perferendis doloribus asperiores repellat. Excepteur sint occaecat cupidatat non proident, sunt in culpa qui officia deserunt mollit anim id est laborum.</p>
</div>
<div class="abs btn-green">Read More</div>

<!-- programs -->
<div class="abs programs-bg" role="img" aria-label="Green-tinted stadium crowd background"></div>
<svg class="abs" style="left:0;top:1660px" width="1200" height="145" viewBox="0 1660 1200 145">
  <polygon points="0,1745 415,1690 785,1690 1200,1745 1200,1760 785,1705 415,1705 0,1760" fill="#fff"/>
  <polygon points="0,1790 415,1712 785,1712 1200,1790 1200,1805 0,1805" fill="#fff"/>
</svg>
<div class="on-green">
  <div class="abs eyebrow" style="top:1508px">Hockey</div>
  <div class="abs rule" style="left:308px;top:1552px;width:87px;background:#fff"></div>
  <div class="abs title" style="top:1535px">Our Programs</div>
  <div class="abs rule" style="left:805px;top:1552px;width:88px;background:#fff"></div>
</div>

<div class="abs card" style="left:110px;top:1598px;width:305px;height:333px">
  <div class="img" role="img" aria-label="Players skating during a program game under arena lights"></div>
  <h3>Itaque Earum Rerum</h3>
  <div class="league">UNVFU - LEAQUE</div>
  <div class="score"><span>USA 7</span><i>FT</i><span>0 CUB</span></div>
</div>
<div class="abs card featured" style="left:446px;top:1598px;width:308px;height:437px">
  <div class="img" role="img" aria-label="Players contesting the puck on the ice"></div>
  <h3>Temporibus Autem</h3>
  <div class="league">JFUHSDN - LEAQUE A</div>
  <div class="score"><span>USA 7</span><i>FT</i><span>0 CUB</span></div>
  <p>Itaque earum rerum hic tenetur a sapiente delectus, ut aut reiciendis voluptatibus maiores alias consequatur aut perferendis doloribus asperiores repellat.</p>
</div>
<div class="abs card" style="left:782px;top:1598px;width:307px;height:333px">
  <div class="img" role="img" aria-label="Skater attacking the goal with a goalie in net" style="background:linear-gradient(180deg,#b9c3cc 0%,#e5e9ed 55%,#f3f5f7 100%)"></div>
  <h3>Itaque Earum Rerum</h3>
  <div class="league">UNVFU - LEAQUE</div>
  <div class="score"><span>USA 7</span><i>FT</i><span>0 CUB</span></div>
</div>

<!-- team -->
<div class="abs eyebrow" style="top:2096px">Bramble</div>
<div class="abs rule" style="left:371px;top:2140px;width:89px"></div>
<div class="abs title" style="top:2123px">Our Team</div>
<div class="abs rule" style="left:740px;top:2140px;width:88px"></div>

<div class="abs member" style="left:112px"><div class="gap"></div><div class="avatar" role="img" aria-label="Portrait of team member Owen Hartley"></div><h4>Owen Hartley</h4><div class="role">Team</div><div class="in">in</div></div>
<div class="abs member" style="left:378px"><div class="gap"></div><div class="avatar" role="img" aria-label="Portrait of team member Miles Carver"></div><h4>Miles Carver</h4><div class="role">Team</div><div class="in">in</div></div>
<div class="abs member" style="left:644px"><div class="gap"></div><div class="avatar" role="img" aria-label="Portrait of team member Theo Ramsey"></div><h4>Theo Ramsey</h4><div class="role">Team</div><div class="in">in</div></div>
<div class="abs member" style="left:910px"><div class="gap"></div><div class="avatar" role="img" aria-label="Portrait of team member Felix Ardent" style="background:linear-gradient(160deg,#e8eddc,#c9a42a 55%,#4a4a2a)"></div><h4>Felix Ardent</h4><div class="role">Team</div><div class="in">in</div></div>

<!-- tournament -->
<div class="abs tour-bg"></div>
<div class="on-green">
  <div class="abs eyebrow" style="top:2553px">Hockey</div>
  <div class="abs rule" style="left:329px;top:2596px;width:87px;background:#fff"></div>
  <div class="abs title" style="top:2580px">Tournament</div>
  <div class="abs rule" style="left:784px;top:2596px;width:88px;background:#fff"></div>
</div>

<div class="abs arrow-btn" style="left:38px"><svg width="12" height="12" viewBox="0 0 12 12"><path d="M8 2L4 6l4 4" stroke="#0b6b12" stroke-width="2" fill="none"/></svg></div>
<div class="abs badge-ring" style="left:111px" role="img" aria-label="Participating team badge"><span></span></div>
<div class="abs" style="left:322px;top:2694px;width:200px;text-align:center;color:#fff">
  <div style="font-size:18px;letter-spacing:1px">★★★★★</div>
  <div class="display" style="font-size:18px;margin-top:2px">Our Reviews</div>
</div>
<div class="abs display" style="left:575px;top:2671px;width:292px;text-align:center;color:#fff;font-size:17px">Date &amp; Time</div>
<div class="abs count" style="left:575px"><b>03</b><small>Day</small></div>
<div class="abs count" style="left:653px"><b>12</b><small>Hours</small></div>
<div class="abs count" style="left:730px"><b>20</b><small>Min</small></div>
<div class="abs count" style="left:808px"><b>10</b><small>Sec</small></div>
<div class="abs badge-ring" style="left:927px" role="img" aria-label="Participating team badge"><span></span></div>
<div class="abs arrow-btn" style="left:1127px"><svg width="12" height="12" viewBox="0 0 12 12"><path d="M4 2l4 4-4 4" stroke="#0b6b12" stroke-width="2" fill="none"/></svg></div>

<!-- footer -->
<div class="abs footer-bg"></div>
<svg class="abs" style="left:0;top:2800px" width="1200" height="200" viewBox="0 2800 1200 200">
  <polygon points="0,2800 1200,2800 1200,2812 900,2915 300,2966 0,2842" fill="#1b851f"/>
  <polygon points="0,2842 300,2966 900,2915 1200,2812 1200,2832 900,2935 300,2986 0,2862" fill="#fff"/>
  <polygon points="0,2862 300,2986 900,2935 1200,2832 1200,3000 0,3000" fill="#000"/>
</svg>
<div class="abs footer-brand">Bramble<br>Hockey</div>
<div class="abs fline" style="top:3091px"></div>

<div class="abs fcol" style="left:113px;top:3146px;width:280px">
  <h5>About Bramble Hockey</h5>
  <p>Itaque earum rerum hic tenetur a sapiente delectus, ut aut reiciendis voluptatibus maiores alias constur repellat.</p>
</div>
<div class="abs social" style="left:111px"></div>
<div class="abs social" style="left:162px"></div>
<div class="abs social" style="left:214px"></div>
<div class="abs social" style="left:267px"></div>

<div class="abs fcol" style="left:442px;top:3143px">
  <h5>Quick Links</h5>
  <ul>
    <li><svg width="14" height="14" viewBox="0 0 14 14"><circle cx="7" cy="7" r="7" fill="#fff"/><path d="M5 4l3 3-3 3" stroke="#000" stroke-width="1.8" fill="none"/></svg>Home</li>
    <li><svg width="14" height="14" viewBox="0 0 14 14"><circle cx="7" cy="7" r="7" fill="#fff"/><path d="M5 4l3 3-3 3" stroke="#000" stroke-width="1.8" fill="none"/></svg>About</li>
    <li><svg width="14" height="14" viewBox="0 0 14 14"><circle cx="7" cy="7" r="7" fill="#fff"/><path d="M5 4l3 3-3 3" stroke="#000" stroke-width="1.8" fill="none"/></svg>Tournament</li>
    <li><svg width="14" height="14" viewBox="0 0 14 14"><circle cx="7" cy="7" r="7" fill="#fff"/><path d="M5 4l3 3-3 3" stroke="#000" stroke-width="1.8" fill="none"/></svg>Team</li>
    <li><svg width="14" height="14" viewBox="0 0 14 14"><circle cx="7" cy="7" r="7" fill="#fff"/><path d="M5 4l3 3-3 3" stroke="#000" stroke-width="1.8" fill="none"/></svg>Contact Us</li>
  </ul>
</div>
<div class="abs fcol" style="left:665px;top:3143px">
  <h5>Help Links</h5>
  <ul>
    <li><svg width="14" height="14" viewBox="0 0 14 14"><circle cx="7" cy="7" r="7" fill="#fff"/><path d="M5 4l3 3-3 3" stroke="#000" stroke-width="1.8" fill="none"/></svg>FAQ</li>
    <li><svg width="14" height="14" viewBox="0 0 14 14"><circle cx="7" cy="7" r="7" fill="#fff"/><path d="M5 4l3 3-3 3" stroke="#000" stroke-width="1.8" fill="none"/></svg>Terms of use</li>
    <li><svg width="14" height="14" viewBox="0 0 14 14"><circle cx="7" cy="7" r="7" fill="#fff"/><path d="M5 4l3 3-3 3" stroke="#000" stroke-width="1.8" fill="none"/></svg>Privacy Policy</li>
    <li><svg width="14" height="14" viewBox="0 0 14 14"><circle cx="7" cy="7" r="7" fill="#fff"/><path d="M5 4l3 3-3 3" stroke="#000" stroke-width="1.8" fill="none"/></svg>Support Links</li>
    <li><svg width="14" height="14" viewBox="0 0 14 14"><circle cx="7" cy="7" r="7" fill="#fff"/><path d="M5 4l3 3-3 3" stroke="#000" stroke-width="1.8" fill="none"/></svg>Conditions</li>
  </ul>
</div>
<div class="abs fcol" style="left:917px;top:3144px">
  <h5>Contact Us</h5>
  <div class="ci" style="margin-top:6px"><span class="ico"><svg width="14" height="16" viewBox="0 0 14 16"><path d="M7 0a6 6 0 0 1 6 6c0 4-6 10-6 10S1 10 1 6a6 6 0 0 1 6-6z" fill="#000"/><circle cx="7" cy="6" r="2.2" fill="#fff"/></svg></span><span>Bramble Hockey<br>United States</span></div>
  <div class="ci" style="margin-top:18px"><span class="ico"><svg width="16" height="16" viewBox="0 0 16 16"><path d="M3 1l3 3-2 2c1 2 3 4 6 6l2-2 3 3-2 2C7 15 1 9 1 3z" fill="#000"/></svg></span><span style="margin-top:3px">+1 888 888 8888</span></div>
  <div class="ci" style="margin-top:18px"><span class="ico"><svg width="16" height="12" viewBox="0 0 16 12"><rect width="16" height="12" rx="1" fill="#000"/><path d="M0 1l8 6 8-6" stroke="#fff" stroke-width="1.4" fill="none"/></svg></span><span style="margin-top:3px">info@bramblehockey.com</span></div>
</div>

<div class="abs fline" style="top:3380px"></div>
<div class="abs copy">Copyrights@2023.Bramble Hockey Development.All Rights Reserved</div>

</body>
</html>
```